Brand Identity Stationary Package

Hello I'm looking for a full branding package for my Property Management Company. I have a logo but looking to have the following
Business Card
Email signature
Facebook cover photo
Letterhead (word.doc)
#10 Envelope
Pocket Folder - link to 9x12 pocket folder design specs https://www.printorbit-example.ca/marketing-materials/presentation-folders
would like everything to match and be brand identifiable. The company looks after residential properties/apartments and some commercial properties. Attached is a zip of the files.
For Business Card
Name: Gareth Lindqvist
Position: Operations Manager
Number: 1 (555) 384-2917
Email: Gareth@harborkey-example.ca
Website: Harborkey-example.ca
Property Management

```html
<!DOCTYPE html>
<html lang="en">
<head>
<meta charset="utf-8">
<title>Harborkey – Email Signature Options</title>
<link href="https://fonts.googleapis.com/css2?family=Roboto:wght@400;500;700&family=Open+Sans:wght@400&display=swap" rel="stylesheet">
<style>
  :root {
    --backdrop: #e8e9ea;
    --card: #ffffff;
    --brand-green: #7cac3a;
    --ink: #1c1c1c;
    --text-grey: #5a5a5a;
    --shadow: rgba(0, 0, 0, 0.28);
  }
  * { box-sizing: border-box; margin: 0; padding: 0; }
  html, body { width: 1200px; height: 1200px; overflow: hidden; }
  body {
    background: var(--backdrop);
    font-family: "Roboto", Arial, sans-serif;
    position: relative;
  }
  .icon-defs { position: absolute; width: 0; height: 0; }

  .option-number {
    position: absolute;
    left: 212px;
    width: 90px;
    text-align: center;
    font-family: "Open Sans", Arial, sans-serif;
    font-size: 92px;
    line-height: 1;
    color: #111;
  }

  .signature-card {
    position: absolute;
    left: 312px;
    width: 576px;
    height: 174px;
    background: var(--card);
    box-shadow: 6px 7px 8px var(--shadow);
  }
  .accent-bar {
    position: absolute;
    left: 0; right: 0; bottom: 0;
    height: 10px;
    background: var(--brand-green);
  }
  .accent-bar--address {
    height: 27px;
    color: #fff;
    font-size: 15px;
    line-height: 27px;
    text-align: center;
  }

  .brand-name {
    position: absolute;
    font-family: "Roboto", Arial, sans-serif;
    font-weight: 700;
    font-size: 29px;
    letter-spacing: 2.5px;
    color: var(--ink);
    line-height: 1;
  }

  .person { position: absolute; }
  .person-name {
    font-weight: 700;
    font-size: 18px;
    color: var(--brand-green);
    line-height: 22px;
  }
  .person-title {
    font-size: 15px;
    color: var(--text-grey);
    line-height: 19px;
  }

  .contact-list { position: absolute; list-style: none; }
  .contact-list li {
    display: flex;
    align-items: center;
    gap: 6px;
    font-size: 15px;
    line-height: 21px;
    color: var(--text-grey);
  }
  .contact-list svg { width: 14px; height: 14px; fill: var(--brand-green); flex: none; }

  .address {
    position: absolute;
    font-size: 15px;
    line-height: 20px;
    color: var(--text-grey);
  }
  .address--right { text-align: right; }
  .address--centered { left: 0; right: 0; text-align: center; }
</style>
</head>
<body>

<svg class="icon-defs" aria-hidden="true">
  <symbol id="icon-phone" viewBox="0 0 24 24">
    <path d="M6.6 10.8a15.1 15.1 0 0 0 6.6 6.6l2.2-2.2a1 1 0 0 1 1-.25 11.4 11.4 0 0 0 3.6.57 1 1 0 0 1 1 1V20a1 1 0 0 1-1 1A17 17 0 0 1 3 4a1 1 0 0 1 1-1h3.5a1 1 0 0 1 1 1c0 1.25.2 2.46.57 3.6a1 1 0 0 1-.25 1z"/>
  </symbol>
  <symbol id="icon-mail" viewBox="0 0 24 24">
    <rect x="1" y="5" width="22" height="14" rx="1"/>
    <path d="M2 6.5l10 7 10-7" fill="none" stroke="#fff" stroke-width="1.8"/>
  </symbol>
  <symbol id="icon-web" viewBox="0 0 24 24">
    <circle cx="12" cy="12" r="11"/>
    <path d="M1 12h22M12 1c3.5 3.5 3.5 18.5 0 22M12 1c-3.5 3.5-3.5 18.5 0 22M3.5 6.5h17M3.5 17.5h17" fill="none" stroke="#fff" stroke-width="1.5"/>
  </symbol>
</svg>

<!-- Option 1 -->
<div class="option-number" style="top:138px;">1</div>
<section class="signature-card" style="top:119px;">
  <div class="person" style="left:40px; top:26px;">
    <p class="person-name">GARETH LINDQVIST</p>
    <p class="person-title">Operations Manager</p>
  </div>
  <ul class="contact-list" style="left:40px; top:84px;">
    <li><svg><use href="#icon-phone"/></svg>1 (555) 384-2917</li>
    <li><svg><use href="#icon-mail"/></svg>Gareth@harborkey-example.ca</li>
    <li><svg><use href="#icon-web"/></svg>www.harborkey-example.ca</li>
  </ul>
  <p class="brand-name" style="right:38px; top:30px;">HARBORKEY</p>
  <p class="address address--right" style="right:38px; top:104px;">14 Larchmont Crescent<br>Alderhaven, NS B3A0Z9</p>
  <div class="accent-bar"></div>
</section>

<!-- Option 2 -->
<div class="option-number" style="top:366px;">2</div>
<section class="signature-card" style="top:317px;">
  <p class="brand-name" style="left:64px; top:72px;">HARBORKEY</p>
  <p class="address" style="left:331px; top:32px;">14 Larchmont Crescent<br>Alderhaven, NS B3A0Z9</p>
  <ul class="contact-list" style="left:331px; top:75px;">
    <li><svg><use href="#icon-phone"/></svg>1 (555) 384-2917</li>
    <li><svg><use href="#icon-mail"/></svg>Gareth@harborkey-example.ca</li>
    <li><svg><use href="#icon-web"/></svg>www.harborkey-example.ca</li>
  </ul>
  <div class="accent-bar"></div>
</section>

<!-- Option 3 -->
<div class="option-number" style="top:563px;">3</div>
<section class="signature-card" style="top:514px;">
  <p class="brand-name" style="left:60px; top:34px;">HARBORKEY</p>
  <div class="person" style="left:60px; top:100px;">
    <p class="person-name">GARETH LINDQVIST</p>
    <p class="person-title">Operations Manager</p>
  </div>
  <p class="address" style="left:335px; top:32px;">14 Larchmont Crescent<br>Alderhaven, NS B3A0Z9</p>
  <ul class="contact-list" style="left:335px; top:75px;">
    <li><svg><use href="#icon-phone"/></svg>1 (555) 384-2917</li>
    <li><svg><use href="#icon-mail"/></svg>Gareth@harborkey-example.ca</li>
    <li><svg><use href="#icon-web"/></svg>www.harborkey-example.ca</li>
  </ul>
  <div class="accent-bar"></div>
</section>

<!-- Option 4 -->
<div class="option-number" style="top:760px;">4</div>
<section class="signature-card" style="top:710px;">
  <p class="brand-name" style="left:60px; top:62px;">HARBORKEY</p>
  <div class="person" style="left:335px; top:24px;">
    <p class="person-name">GARETH LINDQVIST</p>
    <p class="person-title">Operations Manager</p>
  </div>
  <ul class="contact-list" style="left:335px; top:70px;">
    <li><svg><use href="#icon-phone"/></svg>1 (555) 384-2917</li>
    <li><svg><use href="#icon-mail"/></svg>Gareth@harborkey-example.ca</li>
    <li><svg><use href="#icon-web"/></svg>www.harborkey-example.ca</li>
  </ul>
  <p class="address address--centered" style="top:138px;">14 Larchmont Crescent Alderhaven, NS B3A0Z9</p>
  <div class="accent-bar"></div>
</section>

<!-- Option 5 -->
<div class="option-number" style="top:957px;">5</div>
<section class="signature-card" style="top:907px;">
  <p class="brand-name" style="left:60px; top:62px;">HARBORKEY</p>
  <div class="person" style="left:335px; top:24px;">
    <p class="person-name">GARETH LINDQVIST</p>
    <p class="person-title">Operations Manager</p>
  </div>
  <ul class="contact-list" style="left:335px; top:70px;">
    <li><svg><use href="#icon-phone"/></svg>1 (555) 384-2917</li>
    <li><svg><use href="#icon-mail"/></svg>Gareth@harborkey-example.ca</li>
    <li><svg><use href="#icon-web"/></svg>www.harborkey-example.ca</li>
  </ul>
  <div class="accent-bar accent-bar--address">14 Larchmont Crescent Alderhaven, NS B3A0Z9</div>
</section>

</body>
</html>
```